Business Card Design for Marketing Firm

Looking for business card design for higher end marketing firm. Clean but impressionable/trendy. We are a marketing firm that represents manufacturers in the foodservice equipment and supply industry. Our customers are end users such has hotels, restaurants, country clubs, convention centers and casinos as well as distributors of restaurants supplies and equipment, and manufacturers of foodservice equipment and supplies.
Target Market(s)
Hotels, Restaurants, Supply & Equipment Distributors, Foodservice Manufacturers
Industry/Entity Type
Foodservice/Hospitality
Contact Information for Business Card
Name, Title, Contact Number, Email, Website, Social Media, Address
Requirements
Must have
- Clean & Simple but Serious and Impressionable

```html
<!DOCTYPE html>
<html lang="en">
<head>
<meta charset="utf-8">
<title>Northline Hospitality Reps — Business Card</title>
<link rel="stylesheet" href="https://fonts.googleapis.com/css2?family=Montserrat:wght@400;500;700&display=swap">
<style>
  :root {
    --navy: #2a2a78;
    --white: #ffffff;
    --backdrop: #e9e8ee;
    --card-w: 520px;
    --card-h: 300px;
  }
  * { box-sizing: border-box; margin: 0; padding: 0; }
  html, body { width: 1200px; height: 834px; overflow: hidden; }
  body {
    background: var(--backdrop);
    font-family: "Montserrat", sans-serif;
    display: flex;
    align-items: center;
    justify-content: center;
    gap: 56px;
  }
  .card {
    position: relative;
    width: var(--card-w);
    height: var(--card-h);
    border-radius: 26px;
    overflow: hidden;
    background: var(--navy);
    color: var(--white);
    box-shadow: 0 10px 28px rgba(20, 20, 60, 0.18);
  }
  .card__wave { position: absolute; inset: 0; }

  /* Front */
  .person { position: absolute; left: 34px; top: 34px; }
  .person__name { font-weight: 700; font-size: 19px; letter-spacing: 0.5px; }
  .person__title-row { display: flex; align-items: center; gap: 10px; margin-top: 4px; }
  .person__title { font-weight: 400; font-size: 12.5px; letter-spacing: 0.4px; white-space: nowrap; }
  .person__rule { width: 120px; height: 1px; background: var(--white); }
  .contacts { list-style: none; margin-top: 16px; font-size: 12.5px; line-height: 1.7; }
  .contacts li { display: flex; align-items: center; gap: 8px; }
  .contacts svg { width: 12px; height: 12px; fill: var(--white); flex: none; }

  .front-brand {
    position: absolute; right: 30px; top: 52px;
    color: var(--navy); text-align: right;
    font-weight: 500; font-size: 13px; letter-spacing: 1.6px; line-height: 1.5;
  }
  .front-brand__rule { height: 1px; background: var(--navy); margin: 4px 0 3px; }

  .location {
    position: absolute; right: 30px; bottom: 24px;
    text-align: right; font-size: 13px; line-height: 1.45; letter-spacing: 0.3px;
  }

  /* Back */
  .back-brand {
    position: absolute; inset: 0;
    display: flex; flex-direction: column; align-items: center; justify-content: center;
    font-weight: 500; letter-spacing: 3px; text-align: center;
  }
  .back-brand__name { font-size: 24px; }
  .back-brand__rule { width: 330px; height: 1.5px; background: var(--white); margin: 10px 0 8px; }
  .back-brand__sub { font-size: 20px; }
</style>
</head>
<body>

  <section class="card card--front" aria-label="Card front">
    <svg class="card__wave" viewBox="0 0 520 300" preserveAspectRatio="none" aria-hidden="true">
      <path d="M40,0 H520 V222 C430,222 380,175 330,112 C280,50 190,8 40,0 Z" fill="var(--white)"/>
      <path d="M88,0 C215,14 288,62 338,118 C388,172 440,204 520,206" fill="none" stroke="var(--navy)" stroke-width="4"/>
      <path d="M230,52 C290,105 355,178 520,212" fill="none" stroke="var(--navy)" stroke-width="2"/>
    </svg>

    <div class="person">
      <h1 class="person__name">DANIEL REED</h1>
      <div class="person__title-row">
        <p class="person__title">Managing Director</p>
        <span class="person__rule"></span>
      </div>
      <ul class="contacts">
        <li><svg viewBox="0 0 24 24"><path d="M6.6 10.8a15.1 15.1 0 0 0 6.6 6.6l2.2-2.2c.3-.3.7-.4 1-.2 1.1.4 2.3.6 3.6.6.6 0 1 .4 1 1V20c0 .6-.4 1-1 1A17 17 0 0 1 3 4c0-.6.4-1 1-1h3.5c.6 0 1 .4 1 1 0 1.3.2 2.5.6 3.6.1.3 0 .7-.2 1z"/></svg>555.014.2290</li>
        <li><svg viewBox="0 0 24 24"><path d="M7 1h10a2 2 0 0 1 2 2v18a2 2 0 0 1-2 2H7a2 2 0 0 1-2-2V3a2 2 0 0 1 2-2zm0 3v14h10V4zm5 15.5a1 1 0 1 0 0 2 1 1 0 0 0 0-2z"/></svg>555.014.2290</li>
        <li><svg viewBox="0 0 24 24"><path d="M2 5h20v14H2zm2 2v.5l8 5 8-5V7zm0 2.8V17h16V9.8l-8 5z"/></svg>hello@northlinereps.com</li>
      </ul>
    </div>

    <div class="front-brand">
      <p>NORTHLINE HOSPITALITY</p>
      <div class="front-brand__rule"></div>
      <p>REPS</p>
    </div>

    <address class="location" style="font-style:normal">
      northlinereps.com<br>
      418 Maple Ridge Rd<br>
      Dalton, GA 30720
    </address>
  </section>

  <section class="card card--back" aria-label="Card back">
    <div class="back-brand">
      <p class="back-brand__name">NORTHLINE HOSPITALITY</p>
      <div class="back-brand__rule"></div>
      <p class="back-brand__sub">REPS</p>
    </div>
  </section>

</body>
</html>
```